Business Card for premium dental clinic

We are a premium dental clinic based in Brasov, Romania with more than 15 year on the market, providing quality dental treatment made by a team of more specialized dentists, working with modern equipment as a solution to beautiful and healthy teeth.

Our current logo for the clinic use 2 square with colors black and gold - dr Ternisu - studio, using family fonts Bodoni, Myriad Pro and Segoe Print.
Depending on the printing we used some gold CMYK background or gold foil picture background or a gold gradient.
We want a business card:
- eye catching business card
- distinguished business card
- premium design
- to keep the color scheme of black and gold
- to attract the customers to spent time reading the information
- modern concept

```html
<!DOCTYPE html>
<html lang="en">
<head>
<meta charset="UTF-8">
<title>dr Ternisu — Business Card</title>
<link href="https://fonts.googleapis.com/css2?family=Lato:wght@400;700&display=swap" rel="stylesheet">
<style>
  :root {
    --page-bg: #e9e6e1;
    --card-black: #16151a;
    --gold: #bb8c2a;
    --gold-text: #c8962e;
    --light-text: #ece9e4;
    --disc: #f3f2f0;
    --brand-ink: #16151a;
  }
  html, body {
    margin: 0;
    width: 1200px;
    height: 900px;
    overflow: hidden;
    background: var(--page-bg);
  }
  .business-card {
    position: absolute;
    left: 150px;
    top: 172px;
    width: 900px;
    height: 556px;
    background: var(--card-black);
    overflow: hidden;
    box-shadow: 0 18px 40px rgba(0,0,0,0.18);
    font-family: "Lato", Arial, sans-serif;
  }
  .gold-band {
    position: absolute;
    left: 609px;
    top: 0;
    width: 291px;
    height: 100%;
    background: var(--gold);
  }
  .brand-disc {
    position: absolute;
    left: 371px;
    top: 37px;
    width: 480px;
    height: 480px;
    border-radius: 50%;
    background: var(--disc);
    box-shadow: inset 0 0 30px rgba(0,0,0,0.08);
    display: flex;
    align-items: center;
    justify-content: center;
  }
  .brand-name {
    font-family: "Lato", Arial, sans-serif;
    font-weight: 700;
    font-size: 38px;
    color: var(--brand-ink);
    letter-spacing: 0.5px;
  }
  .person-name {
    position: absolute;
    left: 52px;
    top: 60px;
    margin: 0;
    font-family: Arial, "Lato", sans-serif;
    font-weight: 700;
    font-size: 31px;
    color: var(--gold-text);
    letter-spacing: 0.5px;
  }
  .person-role {
    position: absolute;
    left: 52px;
    top: 98px;
    margin: 0;
    font-size: 25px;
    color: var(--light-text);
  }
  .contact-list {
    position: absolute;
    left: 50px;
    top: 298px;
    margin: 0;
    padding: 0;
    list-style: none;
  }
  .contact-item {
    display: flex;
    align-items: center;
    gap: 8px;
    height: 33px;
    font-size: 25px;
    color: var(--light-text);
  }
  .contact-icon {
    width: 20px;
    height: 20px;
    flex: none;
  }
  .address {
    position: absolute;
    left: 54px;
    top: 424px;
    margin: 0;
    font-style: normal;
    font-size: 25px;
    line-height: 33px;
    color: var(--light-text);
  }
</style>
</head>
<body>
  <div class="business-card">
    <div class="gold-band"></div>

    <h1 class="person-name">ANDREI POPESCU</h1>
    <p class="person-role">Managing Director</p>

    <ul class="contact-list">
      <li class="contact-item">
        <svg class="contact-icon" viewBox="0 0 20 20" aria-hidden="true">
          <path fill="var(--gold)" d="M3 7c0-2 3-3 7-3s7 1 7 3v2h-4V7.5H7V9H3z"/>
          <path fill="var(--gold)" d="M5 10h10l2 6H3z"/>
          <circle cx="10" cy="13" r="1.8" fill="var(--card-black)"/>
        </svg>
        040-555 201 734
      </li>
      <li class="contact-item">
        <svg class="contact-icon" viewBox="0 0 20 20" aria-hidden="true">
          <rect x="2" y="4.5" width="16" height="11" fill="var(--gold)"/>
          <path d="M2.5 5l7.5 6 7.5-6" fill="none" stroke="var(--card-black)" stroke-width="1.4"/>
        </svg>
        hello@ternisudental.com
      </li>
      <li class="contact-item">
        <svg class="contact-icon" viewBox="0 0 20 20" aria-hidden="true">
          <circle cx="10" cy="10" r="8" fill="var(--gold)"/>
          <path d="M10 2v16M2 10h16M4.5 5.5c3 2 8 2 11 0M4.5 14.5c3-2 8-2 11 0" fill="none" stroke="var(--card-black)" stroke-width="1"/>
        </svg>
        www.ternisudental.com
      </li>
    </ul>

    <address class="address">421, Address line here,<br>45452,Country Name</address>

    <div class="brand-disc">
      <span class="brand-name">dr Ternisu</span>
    </div>
  </div>
</body>
</html>
```